Photoshop Templates for Instagram, x 2

A Square template to reuse that is on brand.

It will involve an image and text of between 3 and 10 words.
I would like 2 separate contrasting images to use interchangeably

In the files I have added some of the images that I have been using, as well as the home page of my website that is currently being developed.

The on brand would be very recognisable with the website.

Requirements
Must have
• Must be similar in feel to the home page.

Must be simple to to change image and and text in the template

I would like 2 designs. Both similar, but contrasting

The square images show the look that I have been using (created by myself, so I'm sure these can be massively improved upon)

```html
<!DOCTYPE html>
<html lang="en">
<head>
<meta charset="utf-8">
<title>Instagram Quote Templates</title>
<link rel="stylesheet" href="https://fonts.googleapis.com/css2?family=Montserrat:wght@600;700&family=Lato:wght@400&display=swap">
<style>
  :root {
    --sheet-bg: #2b2b2b;
    --ink-black: #000000;
    --quote-cyan: #4fe6ff;
    --name-white: #ffffff;
    --rule-white: rgba(255,255,255,0.85);
    --caption-title: #5f5f5f;
    --caption-sub: #6a6a6a;
    --photo-deep: #062a55;
    --photo-mid: #1677c9;
    --photo-light: #5fd0ff;
  }
  * { margin: 0; padding: 0; box-sizing: border-box; }
  html, body { width: 1062px; height: 1200px; overflow: hidden; }
  body {
    background: radial-gradient(ellipse at center, #333 0%, var(--sheet-bg) 70%);
    position: relative;
    font-family: "Montserrat", sans-serif;
  }
  .template {
    position: absolute;
    width: 417px; height: 417px;
    overflow: hidden;
    box-shadow: 0 8px 24px rgba(0,0,0,0.55);
  }
  .template--right-text { left: 46px; top: 36px; }
  .template--bottom-text { left: 591px; top: 36px; }
  .template--top-text { left: 46px; top: 615px; }
  .template--bottom-left-text { left: 591px; top: 615px; }
  .template__art { position: absolute; inset: 0; width: 100%; height: 100%; display: block; }
  .quote {
    position: absolute;
    font-weight: 600;
    font-size: 25px;
    line-height: 30.6px;
    color: var(--quote-cyan);
    text-transform: uppercase;
    letter-spacing: -0.2px;
    white-space: nowrap;
  }
  .quote--right { text-align: right; }
  .quote--glow { text-shadow: 0 0 10px rgba(79,230,255,0.55); }
  .rule { position: absolute; height: 1px; background: var(--rule-white); }
  .author {
    position: absolute;
    font-weight: 700;
    font-size: 25px;
    line-height: 30px;
    color: var(--name-white);
    text-transform: uppercase;
    letter-spacing: 0.3px;
    white-space: nowrap;
  }
  .author--glow { text-shadow: 0 0 10px rgba(79,230,255,0.6); }
  .caption {
    position: absolute;
    width: 460px;
    text-align: center;
    font-family: "Lato", sans-serif;
  }
  .caption__title { font-size: 37px; line-height: 40px; color: var(--caption-title); }
  .caption__text { font-size: 25px; line-height: 32px; color: var(--caption-sub); margin-top: 4px; }
  .caption--1 { left: 24px; top: 483px; }
  .caption--2 { left: 569px; top: 483px; }
  .caption--3 { left: 24px; top: 1062px; }
  .caption--4 { left: 569px; top: 1062px; }
</style>
</head>
<body>

<!-- Template 1 -->
<section class="template template--right-text">
  <svg class="template__art" viewBox="0 0 417 417">
    <defs>
      <linearGradient id="t1-photo" x1="0" y1="0" x2="1" y2="1">
        <stop offset="0" stop-color="#1a8fe0"/>
        <stop offset="0.35" stop-color="#bff2ff"/>
        <stop offset="0.7" stop-color="#1670c4"/>
        <stop offset="1" stop-color="#061a33"/>
      </linearGradient>
      <linearGradient id="t1-fade" x1="0" y1="0" x2="1" y2="0">
        <stop offset="0" stop-color="#000" stop-opacity="0"/>
        <stop offset="1" stop-color="#000" stop-opacity="1"/>
      </linearGradient>
    </defs>
    <rect width="417" height="417" fill="var(--ink-black)"/>
    <rect width="300" height="417" fill="url(#t1-photo)" role="img" aria-label="Photo of a goalkeeper holding a football, looking up into light"/>
    <rect x="200" width="100" height="417" fill="url(#t1-fade)"/>
    <polygon points="60,0 262,0 262,40 180,100 40,100" fill="#7fe3ff" opacity="0.25"/>
    <polygon points="0,160 120,160 262,260 262,380 0,380" fill="#0a3c7a" opacity="0.25"/>
    <rect x="262" width="155" height="417" fill="var(--ink-black)"/>
  </svg>
  <p class="quote quote--right quote--glow" style="right:14px; top:57px;">“The<br>only way<br>to<br>prove you<br>are a good<br>sport<br>is to lose”</p>
  <div class="rule" style="left:215px; width:186px; top:279px;"></div>
  <p class="author author--glow" style="right:11px; top:286px;">– Rowan Castell</p>
</section>

<!-- Template 2 -->
<section class="template template--bottom-text">
  <svg class="template__art" viewBox="0 0 417 417">
    <defs>
      <radialGradient id="t2-photo" cx="0.55" cy="0.3" r="0.7">
        <stop offset="0" stop-color="#2a9cf0"/>
        <stop offset="0.5" stop-color="#0d4f98"/>
        <stop offset="1" stop-color="#1b2330"/>
      </radialGradient>
      <linearGradient id="t2-band" x1="0" y1="0" x2="0" y2="1">
        <stop offset="0" stop-color="#000" stop-opacity="0.55"/>
        <stop offset="1" stop-color="#000" stop-opacity="0.8"/>
      </linearGradient>
    </defs>
    <rect width="417" height="417" fill="url(#t2-photo)" role="img" aria-label="Close-up portrait photo of an athlete in blue light"/>
    <polygon points="200,0 290,0 417,100 417,170 " fill="#6ad8ff" opacity="0.2"/>
    <polygon points="15,168 417,168 417,220 90,220" fill="#3fd3ff" opacity="0.35"/>
    <rect y="257" width="417" height="160" fill="url(#t2-band)"/>
  </svg>
  <p class="quote quote--right" style="right:12px; top:271px;">“It is not the size of a man<br>but the size of his heart<br>that matters.”</p>
  <div class="rule" style="left:221px; width:178px; top:365px;"></div>
  <p class="author" style="right:18px; top:370px;">Damon Ashcroft</p>
</section>

<!-- Template 3 -->
<section class="template template--top-text">
  <svg class="template__art" viewBox="0 0 417 417">
    <defs>
      <linearGradient id="t3-photo" x1="0" y1="0" x2="0" y2="1">
        <stop offset="0" stop-color="#000"/>
        <stop offset="0.2" stop-color="#000"/>
        <stop offset="0.38" stop-color="#155fae"/>
        <stop offset="0.6" stop-color="#5fb8e8"/>
        <stop offset="0.85" stop-color="#12315a"/>
        <stop offset="1" stop-color="#050a14"/>
      </linearGradient>
    </defs>
    <rect width="417" height="417" fill="url(#t3-photo)" role="img" aria-label="Action photo of a footballer performing an overhead kick"/>
    <polygon points="0,110 60,90 300,330 220,417 0,417" fill="#1aa6ff" opacity="0.3"/>
    <polygon points="240,150 417,150 417,300 330,360" fill="#dff6ff" opacity="0.25"/>
  </svg>
  <p class="quote quote--right" style="right:22px; top:20px;">“If you fail to prepare,<br>you’re prepared to fail”</p>
  <div class="rule" style="left:212px; width:178px; top:83px;"></div>
  <p class="author" style="right:28px; top:87px;">– Luke Tremaine</p>
</section>

<!-- Template 4 -->
<section class="template template--bottom-left-text">
  <svg class="template__art" viewBox="0 0 417 417">
    <defs>
      <linearGradient id="t4-photo" x1="0" y1="0" x2="1" y2="1">
        <stop offset="0" stop-color="#0d3f7e"/>
        <stop offset="0.45" stop-color="#2a8fdc"/>
        <stop offset="0.75" stop-color="#1a5ea6"/>
        <stop offset="1" stop-color="#07162b"/>
      </linearGradient>
      <linearGradient id="t4-shade" x1="0" y1="0" x2="0" y2="1">
        <stop offset="0.55" stop-color="#000" stop-opacity="0"/>
        <stop offset="1" stop-color="#000" stop-opacity="0.7"/>
      </linearGradient>
    </defs>
    <rect width="417" height="417" fill="url(#t4-photo)" role="img" aria-label="Portrait photo of a man in a jacket speaking"/>
    <polygon points="150,0 240,0 417,160 417,280" fill="#7fdcff" opacity="0.2"/>
    <polygon points="0,130 0,250 180,417 260,417" fill="#5cc8ff" opacity="0.2"/>
    <rect width="417" height="417" fill="url(#t4-shade)"/>
  </svg>
  <p class="quote" style="left:24px; top:171px;">“It is not the<br>size of a man<br>but the size<br>of his heart<br>that<br>matters.”</p>
  <div class="rule" style="left:25px; width:184px; top:353px;"></div>
  <p class="author" style="left:25px; top:360px;">Damon Ashcroft</p>
</section>

<div class="caption caption--1">
  <h2 class="caption__title">Template style 1</h2>
  <p class="caption__text">with text at right side suitable for portrait image</p>
</div>
<div class="caption caption--2">
  <h2 class="caption__title">Template style 2</h2>
  <p class="caption__text">with text at bottom suitable for<br>landscape image</p>
</div>
<div class="caption caption--3">
  <h2 class="caption__title">Template style 3</h2>
  <p class="caption__text">with text at top suitable for<br>landscape image</p>
</div>
<div class="caption caption--4">
  <h2 class="caption__title">Template style 4</h2>
  <p class="caption__text">with text at bottom left suitable for<br>portrait image</p>
</div>

</body>
</html>
```